KDN Roofing Truck and Trailer Wrap

I need a graphic wrap on my Toyota Tundra pickup truck, and our 14' enclosed trailer

Target Market(s)

Home Owners

Industry/Entity Type

Roofing

Requirements
Must have
• Harwell Siding Supply and TBR Logos
Nice to have
• Our services listed somewhere on the truck, maybe on the back tailgate and also on the sides at the very bottom of the doors: Roofing, Siding, Gutters, Painting

```html
<!DOCTYPE html>
<html lang="en">
<head>
<meta charset="utf-8">
<title>Kendall Property Services – Truck Wrap</title>
<link rel="stylesheet" href="https://fonts.googleapis.com/css2?family=Libre+Caslon+Text:wght@700&family=Poppins:wght@500;600;700&display=swap">
<style>
  :root {
    --bg: #e8e8ec;
    --wrap-black: #0b0b0c;
    --wrap-navy: #0e1421;
    --wrap-white: #ffffff;
    --gold: #e8a21c;
    --orange-url: #d2470f;
    --ink: #111111;
    --light: #f4f4f4;
  }
  html, body {
    margin: 0;
    width: 937px;
    height: 1200px;
    overflow: hidden;
    background: var(--bg);
  }
  .sheet { position: relative; width: 937px; height: 1200px; }
  .panel { position: absolute; display: block; }
  .side-driver { left: 20px; top: 30px; }
  .side-passenger { left: 20px; top: 400px; }
  .tailgate { left: 20px; top: 800px; }
  .hood { left: 487px; top: 800px; }

  .brand-name { font-family: "Libre Caslon Text", Georgia, serif; font-weight: 700; }
  .brand-sub { font-family: "Libre Caslon Text", Georgia, serif; font-weight: 700; letter-spacing: 0.3em; }
  .url { font-family: "Poppins", Arial, sans-serif; font-weight: 700; }
  .services { font-family: "Poppins", Arial, sans-serif; font-weight: 600; }
  .phone { font-family: "Poppins", Arial, sans-serif; font-weight: 600; }
  .partner { font-family: "Poppins", Arial, sans-serif; font-weight: 600; }
</style>
</head>
<body>
<main class="sheet">

  <!-- Driver side -->
  <svg class="panel side-driver" width="897" height="330" viewBox="0 0 900 330" aria-label="Driver side wrap layout">
    <rect width="900" height="330" rx="18" fill="var(--wrap-black)"/>
    <polygon points="0,110 420,110 480,40 570,330 0,330" fill="var(--wrap-white)"/>
    <polyline points="0,110 420,110 480,40 570,330" fill="none" stroke="var(--gold)" stroke-width="6"/>
    <text class="brand-name" x="210" y="222" font-size="76" fill="var(--ink)" text-anchor="middle">Kendall</text>
    <rect x="395" y="165" width="60" height="60" fill="var(--gold)"/>
    <text class="brand-sub" x="210" y="256" font-size="18" fill="var(--ink)" text-anchor="middle">PROPERTY SERVICES</text>
    <text class="url" x="210" y="292" font-size="26" fill="var(--orange-url)" text-anchor="middle">www.kdnroofing.com</text>
    <text class="services" x="885" y="82" font-size="18" fill="var(--gold)" text-anchor="end">Roofing - Siding - Gutters - Painting</text>
    <text class="phone" x="800" y="142" font-size="34" fill="var(--light)" text-anchor="end">317-555-0148</text>
    <text class="partner" x="885" y="200" font-size="14" fill="var(--light)" text-anchor="end">Harwell Siding Supply</text>
    <text class="partner" x="885" y="230" font-size="18" fill="var(--light)" text-anchor="end">TBR</text>
  </svg>

  <!-- Passenger side -->
  <svg class="panel side-passenger" width="897" height="330" viewBox="0 0 900 330" aria-label="Passenger side wrap layout">
    <rect width="900" height="330" rx="18" fill="var(--wrap-black)"/>
    <polygon points="900,110 480,110 420,40 330,330 900,330" fill="var(--wrap-white)"/>
    <polyline points="900,110 480,110 420,40 330,330" fill="none" stroke="var(--gold)" stroke-width="6"/>
    <rect x="445" y="165" width="60" height="60" fill="var(--gold)"/>
    <text class="brand-name" x="690" y="222" font-size="76" fill="var(--ink)" text-anchor="middle">Kendall</text>
    <text class="brand-sub" x="690" y="256" font-size="18" fill="var(--ink)" text-anchor="middle">PROPERTY SERVICES</text>
    <text class="url" x="690" y="292" font-size="26" fill="var(--orange-url)" text-anchor="middle">www.kdnroofing.com</text>
    <text class="services" x="15" y="82" font-size="18" fill="var(--gold)">Roofing - Siding - Gutters - Painting</text>
    <text class="phone" x="100" y="142" font-size="34" fill="var(--light)">317-555-0148</text>
    <text class="partner" x="15" y="200" font-size="14" fill="var(--light)">Harwell Siding Supply</text>
    <text class="partner" x="15" y="230" font-size="18" fill="var(--light)">TBR</text>
  </svg>

  <!-- Tailgate -->
  <svg class="panel tailgate" width="450" height="360" viewBox="0 0 450 360" aria-label="Tailgate wrap layout">
    <rect width="450" height="360" rx="16" fill="var(--wrap-navy)"/>
    <text class="services" x="24" y="48" font-size="22" fill="var(--light)">kdnroofing.com</text>
    <text class="phone" x="426" y="48" font-size="22" fill="var(--light)" text-anchor="end">317-555-0148</text>
    <rect x="30" y="130" width="60" height="60" fill="var(--gold)"/>
    <text class="brand-name" x="212" y="175" font-size="46" fill="var(--light)" text-anchor="middle">Kendall</text>
    <text class="brand-sub" x="212" y="202" font-size="11" fill="var(--light)" text-anchor="middle">PROPERTY SERVICES</text>
    <text class="partner" x="426" y="146" font-size="12" fill="var(--light)" text-anchor="end">Harwell Siding</text>
    <text class="partner" x="426" y="162" font-size="12" fill="var(--light)" text-anchor="end">Supply</text>
    <text class="partner" x="426" y="192" font-size="18" fill="var(--light)" text-anchor="end">TBR</text>
    <polygon points="40,250 420,250 400,300 20,300" fill="var(--gold)"/>
    <text class="services" x="220" y="283" font-size="19" fill="var(--ink)" text-anchor="middle">Roofing - Siding - Gutters - Painting</text>
  </svg>

  <!-- Hood -->
  <svg class="panel hood" width="430" height="360" viewBox="0 0 430 360" aria-label="Hood wrap layout">
    <path d="M50,20 H380 Q420,20 425,80 L430,340 H0 L5,80 Q10,20 50,20 Z" fill="var(--wrap-black)"/>
    <rect x="105" y="160" width="44" height="44" fill="var(--gold)"/>
    <text class="brand-name" x="240" y="190" font-size="40" fill="var(--light)" text-anchor="middle">Kendall</text>
    <text class="brand-sub" x="240" y="210" font-size="9" fill="var(--light)" text-anchor="middle">PROPERTY SERVICES</text>
  </svg>

</main>
</body>
</html>
```